Business Card Design

I am a vocalist and songwriter. I am an alternative soul singer, but there are definitely some jazz elements as well. It would probably be easiest to go to my website to get an idea about my design needs.
www.corinnethaleby.com
I would like to continue the theme on the first page in the green dress and orchard.
I am not sure if double sided is necessary. I was thinking a qr code to scan and go to the website would be nice. I am not sure if it's necessary.
The font for Past Midnight is Rockwell.
Also, I need something else please let me know or you think the QR code is viable, I can upload that as well.
Thanks!
NOTE TO DESIGNERS FROM PH ADMIN:
The business cards for this project should be formatted according to the U.S. template (see links below):
http://files.pixelharbor-example.com/print_template/vp/pixelharbor_usa_businesscard_printready_cmyk_ai.zip
http://files.pixelharbor-example.com/print_template/vp/pixelharbor_usa_businesscard_printready_cmyk_psd.zip
Updates
I have added a psd file which has the logo in it.
I really would like a two sided card with the QR code on the back. That is included in the files
Also, I have included the rockwell font zip file which is the same font used on my website.
Thanks!
Industry/Entity Type
Business
Contact Information for Business Card
Corinne Thaleby
Vocalist/Songwriter
1 (555) 014-7380
info@corinnethaleby.com
www.corinnethaleby.com
Look and feel

```html
<!DOCTYPE html>
<html lang="en">
<head>
<meta charset="utf-8">
<title>Corinne Thaleby – Business Card</title>
<link rel="stylesheet" href="https://fonts.googleapis.com/css2?family=Exo+2:wght@300;400;500&family=Kaushan+Script&display=swap">
<style>
  :root {
    --backdrop: #d9d6d1;
    --dress-green: #3f9a3a;
    --grass-gold: #7a6535;
    --orchard-brown: #3a2d1c;
    --orchard-dark: #1a140d;
    --apple-red: #9a2a1c;
    --crate-wood: #5a3b22;
    --panel: rgba(18, 14, 10, 0.78);
    --icon-green: #5bb84a;
    --ink-light: #ffffff;
    --ink-soft: #ecebe6;
  }
  * { box-sizing: border-box; }
  html, body {
    margin: 0;
    width: 1200px;
    height: 873px;
    overflow: hidden;
    background: var(--backdrop);
  }
  .canvas {
    position: relative;
    width: 1200px;
    height: 873px;
  }
  .business-card {
    position: absolute;
    left: 75px;
    top: 136px;
    width: 1050px;
    height: 600px;
    overflow: hidden;
    box-shadow: 0 12px 30px rgba(0,0,0,0.25);
    font-family: "Exo 2", sans-serif;
    background: var(--orchard-dark);
  }
  .orchard-photo {
    position: absolute;
    inset: 0;
    background:
      radial-gradient(ellipse 210px 150px at 420px 520px, var(--apple-red) 0%, var(--crate-wood) 55%, transparent 100%),
      radial-gradient(ellipse 330px 300px at 230px 250px, var(--dress-green) 0%, rgba(63,154,58,0.85) 45%, transparent 100%),
      linear-gradient(100deg, var(--grass-gold) 0%, var(--orchard-brown) 55%, var(--orchard-dark) 100%);
  }
  .identity {
    position: absolute;
    left: 590px;
    top: 40px;
    width: 430px;
    color: var(--ink-light);
  }
  .identity__name {
    margin: 0;
    font-family: "Kaushan Script", cursive;
    font-weight: 400;
    font-size: 70px;
    line-height: 0.95;
  }
  .identity__name-last {
    display: block;
    padding-left: 30px;
  }
  .identity__swoosh {
    display: block;
    margin: 4px 0 0 60px;
  }
  .identity__role {
    margin: 8px 0 0;
    font-weight: 400;
    font-size: 32px;
    color: var(--ink-soft);
  }
  .contact-panel {
    position: absolute;
    left: 540px;
    top: 330px;
    width: 420px;
    padding: 20px 24px;
    border-radius: 14px;
    background: var(--panel);
    list-style: none;
    margin: 0;
  }
  .contact-panel__item {
    display: flex;
    align-items: center;
    gap: 16px;
    height: 50px;
    font-size: 24px;
    color: var(--ink-soft);
    white-space: nowrap;
  }
  .contact-panel__icon {
    flex: none;
    width: 34px;
    height: 34px;
  }
</style>
</head>
<body>
<main class="canvas">
  <article class="business-card">
    <div class="orchard-photo" role="img" aria-label="Photograph of the singer in a long green dress standing in an apple orchard holding a red apple, with a wooden crate of red apples at her feet"></div>

    <header class="identity">
      <h1 class="identity__name">Corinne <span class="identity__name-last">Thaleby</span></h1>
      <svg class="identity__swoosh" width="280" height="24" viewBox="0 0 280 24" aria-hidden="true">
        <path d="M4 6 C 90 20, 190 22, 276 10" fill="none" stroke="var(--ink-light)" stroke-width="2.5" stroke-linecap="round"/>
      </svg>
      <p class="identity__role">Vocalist/Songwriter</p>
    </header>

    <ul class="contact-panel">
      <li class="contact-panel__item">
        <svg class="contact-panel__icon" viewBox="0 0 34 34" aria-hidden="true">
          <circle cx="17" cy="17" r="17" fill="var(--icon-green)"/>
          <rect x="9" y="11" width="16" height="12" rx="1.5" fill="none" stroke="#fff" stroke-width="2"/>
          <path d="M9.5 12 L17 18 L24.5 12" fill="none" stroke="#fff" stroke-width="2"/>
        </svg>
        <span>info@corinnethaleby.com</span>
      </li>
      <li class="contact-panel__item">
        <svg class="contact-panel__icon" viewBox="0 0 34 34" aria-hidden="true">
          <circle cx="17" cy="17" r="17" fill="var(--icon-green)"/>
          <path d="M17 8 C12.5 8 10 11.2 10 14.5 C10 19 17 26 17 26 C17 26 24 19 24 14.5 C24 11.2 21.5 8 17 8 Z" fill="#fff"/>
          <circle cx="17" cy="14.5" r="2.6" fill="var(--icon-green)"/>
        </svg>
        <span>www.corinnethaleby.com</span>
      </li>
      <li class="contact-panel__item">
        <svg class="contact-panel__icon" viewBox="0 0 34 34" aria-hidden="true">
          <circle cx="17" cy="17" r="17" fill="var(--icon-green)"/>
          <path d="M12 9 L15 9 L16.5 13.5 L14.5 15 C15.5 17.5 16.5 18.5 19 19.5 L20.5 17.5 L25 19 L25 22 C25 23.5 23.5 25 22 25 C15 24.5 9.5 19 9 12 C9 10.5 10.5 9 12 9 Z" fill="#fff"/>
        </svg>
        <span>(555) 014-7380</span>
      </li>
    </ul>
  </article>
</main>
</body>
</html>
```